Yard sign design for high end luxury home builder.

Need a design for signage on custom homes that are being built. I already have a logo that I am satisfied with that needs to be incorporated. I need the following incorporated in the design of the sign-
- Lic number 381526
- phone number (805) 555-0148‬
- quennbuilderscrew.com
- Logo/Branding

If possible it may be nice to have the following quote that is on are business cards-

Quote from Gerard of Norvelle-
HE WHO WORKS WITH HIS HANDS IS A LABORER.
HE WHO WORKS WITH HIS HANDS & HIS HEAD IS A CRAFTSMAN.
HE WHO WORKS WITH HIS HANDS & HIS HEAD & HIS HEART IS AN ARTISAN.
-GERARD OF NORVELLE

Target Market(s)

Archetect, Designers, Clients desiring to build a new home or remodel.

Colors
fde9d4
fee4d5
fabb94
fac994
faa54b
f68d4d
f37122
f78f20
f68e4e

Requirements
Must have
• - Lic number 381526
• - phone number (805) 555-0148‬
• - quennbuilderscrew.com
• - Logo/Branding
Nice to have
• Quote from Gerard of Norvelle-
• HE WHO WORKS WITH HIS HANDS IS A LABORER.
• HE WHO WORKS WITH HIS HANDS & HIS HEAD IS A CRAFTSMAN.
• HE WHO WORKS WITH HIS HANDS & HIS HEAD & HIS HEART IS AN ARTISAN.
• -GERARD OF NORVELLE
• OR the below statement-
• Craftsmen that Care
Should not have
• Any additional verbiage not specified above including any type of verbiage about what kind of company we are. For instance- Integrity, reputable... It's just all played out. Im just looking for a bitching design that has the info that compliments my logo/branding.

```html
<!DOCTYPE html>
<html lang="en">
<head>
<meta charset="utf-8">
<title>Quenn Builders Yard Sign</title>
<link rel="stylesheet" href="https://fonts.googleapis.com/css2?family=Crimson+Text:ital,wght@0,400;0,600;0,700;1,600;1,700&display=swap">
<style>
  :root {
    --ink: #4a3426;
    --stone-light: #f1f0ee;
    --stone-mid: #e2e0dc;
    --brand-wood: #7a5a3e;
    --page: #ffffff;
    --on-ink: #ffffff;
  }
  html, body {
    margin: 0;
    padding: 0;
    width: 1200px;
    height: 1200px;
    overflow: hidden;
    background: var(--page);
  }
  .canvas {
    position: relative;
    width: 1200px;
    height: 1200px;
    font-family: "Crimson Text", Georgia, serif;
    color: var(--ink);
  }
  .sign {
    position: absolute;
    left: 86px;
    top: 214px;
    width: 1020px;
    height: 760px;
    background: radial-gradient(ellipse at 40% 40%, var(--stone-light) 0%, var(--stone-mid) 100%);
  }
  .sign-frame {
    position: absolute;
    left: 14px;
    top: 12px;
    width: 988px;
    height: 734px;
    border: 2px solid var(--ink);
    box-sizing: border-box;
  }
  .license {
    position: absolute;
    left: 80px;
    top: 38px;
    font-size: 20px;
    font-weight: 700;
    font-variant-numeric: oldstyle-nums;
  }
  .brand {
    position: absolute;
    left: 78px;
    top: 78px;
    width: 330px;
  }
  .brand-mark {
    width: 290px;
    height: 290px;
    margin-left: 20px;
    background: var(--brand-wood);
  }
  .brand-name {
    margin-top: 24px;
    text-align: center;
    font-weight: 700;
    line-height: 1;
    letter-spacing: 3px;
  }
  .brand-name .primary { display: block; font-size: 56px; }
  .brand-name .secondary { display: block; font-size: 22px; margin-top: 6px; letter-spacing: 2px; }
  .headline {
    position: absolute;
    left: 494px;
    top: 44px;
    margin: 0;
    font-size: 94px;
    font-weight: 400;
    line-height: 92px;
  }
  .quote {
    position: absolute;
    left: 514px;
    top: 290px;
    width: 450px;
    margin: 0;
    font-size: 18.5px;
    font-weight: 700;
    font-style: italic;
    line-height: 23px;
  }
  .quote-mark {
    position: absolute;
    font-size: 44px;
    line-height: 1;
  }
  .quote-mark.open { left: -32px; top: -6px; }
  .quote-mark.close { position: relative; top: 10px; margin-left: 4px; font-size: 40px; }
  .quote-source {
    position: absolute;
    left: 514px;
    top: 432px;
    font-size: 18px;
    font-weight: 600;
    font-style: italic;
  }
  .phone {
    position: absolute;
    left: 70px;
    top: 480px;
    font-size: 150px;
    font-weight: 400;
    line-height: 1;
    letter-spacing: 1px;
    font-variant-numeric: oldstyle-nums;
    white-space: nowrap;
  }
  .web {
    position: absolute;
    left: 266px;
    top: 686px;
    width: 488px;
    height: 60px;
    background: var(--ink);
    color: var(--on-ink);
    border-radius: 22px 22px 0 0;
    text-align: center;
    font-size: 38px;
    line-height: 60px;
  }
</style>
</head>
<body>
<div class="canvas">
  <section class="sign">
    <div class="sign-frame"></div>
    <div class="license">Lic 381526</div>
    <div class="brand">
      <div class="brand-mark"></div>
      <div class="brand-name">
        <span class="primary">QUENN</span>
        <span class="secondary">BUILDERS INC.</span>
      </div>
    </div>
    <h1 class="headline">Craftsmen<br>That Care</h1>
    <blockquote class="quote">
      <span class="quote-mark open">&ldquo;</span>
      He who works with his hands is a laborer.<br>
      He who works with his hands &amp; his head<br>
      is a craftsman.<br>
      He who works with his hands &amp; his head<br>
      &amp; his heart is an artisan.<span class="quote-mark close">&rdquo;</span>
    </blockquote>
    <div class="quote-source">- Gerard of Norvelle</div>
    <div class="phone">(805) 555 0148</div>
    <div class="web">quennbuilderscrew.com</div>
  </section>
</div>
</body>
</html>
```